RWT Fittings Ltd Business Cards

We need a business card with our business logo. We provide window and door installations on high-rises in west coast British Colombia, Canada.

I would like my business information and details on one side of the card, and the other side the company name with logo

Target Market(s)

General Contractors

Industry/Entity Type

Construction

Contact Information for Business Card

one side i want my company name and logo in the dark theme logo that i provided

Requirements
Must have
• Marco Peltieri, 16045518293, RWTFittings@mailbox-demo.com, 1407-5194 Linden Row Burnaby BC, V5H 2K9, Owner & Manager

```html
<!DOCTYPE html>
<html lang="en">
<head>
<meta charset="utf-8">
<title>RWT Fittings Ltd — Business Cards</title>
<link rel="stylesheet" href="https://fonts.googleapis.com/css2?family=Poppins:wght@500;600&family=Roboto:wght@400&display=swap">
<style>
  :root {
    --page: #242426;
    --card: #1f1f23;
    --card-deep: #141417;
    --blue: #29a8e0;
    --grey: #a7a7a9;
    --white: #f2f2f2;
    --shade-light: #3a3a3f;
  }
  * { margin: 0; padding: 0; box-sizing: border-box; }
  html, body {
    width: 1200px;
    height: 780px;
    overflow: hidden;
    background: var(--page);
  }
  .canvas {
    width: 1200px;
    height: 780px;
    display: flex;
    align-items: center;
    justify-content: center;
    gap: 40px;
  }
  .card {
    position: relative;
    width: 560px;
    height: 320px;
    background: var(--card);
    overflow: hidden;
    box-shadow: 0 18px 40px rgba(0,0,0,0.45);
  }

  /* Front side */
  .brand {
    position: absolute;
    left: 180px;
    top: 52px;
    display: flex;
    align-items: center;
    gap: 12px;
  }
  .brand-mark {
    width: 30px;
    height: 30px;
    background: var(--blue);
  }
  .brand-name {
    font-family: "Poppins", sans-serif;
    font-weight: 600;
    font-size: 30px;
    line-height: 1;
    color: var(--blue);
    letter-spacing: 0.5px;
  }
  .contact {
    position: absolute;
    left: 40px;
    top: 128px;
    font-family: "Roboto", sans-serif;
    font-size: 12.5px;
    line-height: 1.45;
    color: var(--white);
    list-style: none;
  }
  .contact li { display: flex; align-items: center; gap: 6px; }
  .contact .address { display: block; padding-left: 18px; margin-bottom: 2px; }
  .contact svg { width: 12px; height: 12px; flex: none; }
  .person {
    position: absolute;
    right: 30px;
    top: 142px;
    text-align: right;
    font-family: "Poppins", sans-serif;
  }
  .person-name {
    font-size: 24px;
    font-weight: 600;
    line-height: 1.1;
    color: var(--grey);
  }
  .person-name .first { color: var(--blue); }
  .person-role {
    font-size: 13px;
    font-weight: 500;
    color: var(--white);
    margin-top: 2px;
  }
  .accent-bar {
    position: absolute;
    right: 0;
    top: 186px;
    width: 18px;
    height: 34px;
    background: var(--blue);
  }
  .front-emblem-area {
    position: absolute;
    left: 220px;
    bottom: 0;
    width: 320px;
    height: 120px;
    background: linear-gradient(120deg, var(--card-deep) 0%, #18181c 60%, var(--shade-light) 100%);
  }

  /* Back side */
  .back-pattern-area {
    position: absolute;
    inset: 0;
    background: linear-gradient(225deg, #4a4a50 0%, #26262a 30%, var(--card-deep) 60%, #18181b 100%);
  }
  .back-brand {
    position: absolute;
    left: 330px;
    top: 226px;
    display: flex;
    align-items: center;
    gap: 6px;
  }
  .back-brand .brand-mark { width: 14px; height: 14px; }
  .back-brand .brand-name { font-size: 14px; }
</style>
</head>
<body>
<main class="canvas">

  <section class="card card-front" aria-label="Business card front">
    <div class="brand">
      <span class="brand-mark"></span>
      <span class="brand-name">RWT Fittings Ltd</span>
    </div>

    <ul class="contact">
      <li class="address">1407-5194 Linden Row<br>Burnaby BC, V5H 2K9</li>
      <li>
        <svg viewBox="0 0 24 24" aria-hidden="true"><path fill="#29a8e0" d="M6.6 10.8a15.1 15.1 0 0 0 6.6 6.6l2.2-2.2a1 1 0 0 1 1-.25 11.4 11.4 0 0 0 3.6.57 1 1 0 0 1 1 1V20a1 1 0 0 1-1 1A17 17 0 0 1 3 4a1 1 0 0 1 1-1h3.5a1 1 0 0 1 1 1c0 1.25.2 2.45.57 3.57a1 1 0 0 1-.25 1z"/></svg>
        <span>1604 551 8293</span>
      </li>
      <li>
        <svg viewBox="0 0 24 24" aria-hidden="true"><rect x="2" y="5" width="20" height="14" rx="2" fill="#29a8e0"/><path d="M3 6l9 7 9-7" fill="none" stroke="#1f1f23" stroke-width="2"/></svg>
        <span>RWTFittings@mailbox-demo.com</span>
      </li>
    </ul>

    <div class="person">
      <p class="person-name"><span class="first">Marco</span> Peltieri</p>
      <p class="person-role">Owner &amp; Manager</p>
    </div>
    <span class="accent-bar"></span>

    <div class="front-emblem-area" role="img" aria-label="Large embossed company emblem in dark tones"></div>
  </section>

  <section class="card card-back" aria-label="Business card back">
    <div class="back-pattern-area" role="img" aria-label="Repeating glossy company emblem pattern on dark background"></div>
    <div class="back-brand">
      <span class="brand-mark"></span>
      <span class="brand-name">RWT Fittings Ltd</span>
    </div>
  </section>

</main>
</body>
</html>
```